Cover for nonfiction/memoir book "Quiet Rooms Within"

Revisions only please.

We're looking for a *nonfiction* *memoir* look that is consistent with other covers in that genre.

MUST HAVE:
- It must include the BACK COVER as it will be for print as well as an ebook.
- Title: Quiet Rooms Within
- TITLE MUST BE EASILY READ AT BOOKARA THUMBNAIL SIZE
- Author name: Daphne Korrel
- At least one of the attached photos of Daphne
- In COLOR
- The synopsis below
- Space for an endorsement

From the author: "I am looking for a cover that is eye catching and interesting or artistic, rather than just glamorous or pretty. If you like to edit the photos please do not completely remove the wrinkle between my eyebrows as I mention this in the book. It is okay if i look non conventional and my inner Aspie shows a little. The book is a little bit girly, and it would be good for the cover to reflect that, but mildly. No bright pink and purple designs. Please feel free to zoom in or crop the photos as you think works best"

SYNOPSIS (needs to go on the back cover)

Quiet Rooms Within is an acutely honest and often highly entertaining memoir by Daphne Korrel about life with Asperger's Syndrome. The book follows Daphne in exploring her past and takes the reader with her on her journey to receiving and accepting her diagnosis. Instead of rehashing widely available Asperger's information, Daphne focuses on discussing the thoughts, feelings and ideas that go along with being an Aspie, giving us a rare peek into what it really feels like to be a person on the spectrum. A must read for all those who enjoy deep personal stories or have a loved one on the spectrum that they wish to understand better.

The book dimensions will be 5x8 trade paperback and 6x9 hardcover (plus 0.25 bleed margin on all sizes - for both sizes).
Here is some more information from the publisher on cover requirements:

"I've attached a sample of both a paperback and hardcover size. Note that the spine width will be different depending on the final length of the book, so it won't be exact. That said, the front and back covers, and the flaps (for the hardcover) will always be the same as shown.
For deliverables, we need the following:

a Design Studio 6 or earlier native .PSD (Photoshop), .ID (InDesign), or .AI (Illustrator) file. Design Sky files cannot be used and will not be accepted.
final file must include layered objects, and cannot be one 'background' image
Final files must be in CMYK color mode, 300dpi minimum
Total Ink saturation must be no more than 240% on any part of the cover. "True" black should use the following CMYK values: 60/40/40/100.
Fonts used in creation of the cover must be either A) embedded or B) sent with the final file
Vector art is preferred for scaling purposes"

Target Market(s)

Women of all ages. People who like psychology and personal stories.
Also parents and family members who may have a loved one on the Autism spectrum.

Requirements
Nice to have
• Bright green new leaves and greenery are good but not necessary.

```html
<!DOCTYPE html>
<html lang="en">
<head>
<meta charset="utf-8">
<title>Quiet Rooms Within — Back Cover and Spine</title>
<link rel="stylesheet" href="https://fonts.googleapis.com/css2?family=Cinzel:wght@400;600&family=Open+Sans:wght@400;600&display=swap">
<style>
  :root {
    --canvas-bg: #e9e9e7;
    --cover-light: #c9d96a;
    --cover-mid: #b3c84a;
    --cover-deep: #9bb23a;
    --band-green: #2f6a2c;
    --spine-green: #2c6a2a;
    --ink: #1f2a12;
    --paper-white: #ffffff;
    --leaf-light: #d8ec7a;
    --leaf-deep: #6f9a2c;
    --sky-blue: #a9c9c4;
  }
  * { box-sizing: border-box; margin: 0; padding: 0; }
  html, body {
    width: 1200px;
    height: 1072px;
    overflow: hidden;
    background: var(--canvas-bg);
  }
  .book-wrap {
    position: absolute;
    left: 270px;
    top: 88px;
    width: 660px;
    height: 896px;
    display: flex;
    box-shadow: 0 18px 40px rgba(0,0,0,0.12);
  }
  .back-cover {
    position: relative;
    width: 560px;
    height: 896px;
    background: linear-gradient(180deg, var(--cover-light) 0%, var(--cover-mid) 55%, var(--cover-deep) 100%);
    overflow: hidden;
  }
  .leaf-photo {
    position: absolute;
    left: 0; top: 0;
    width: 560px;
    height: 200px;
    background:
      radial-gradient(ellipse at 78% 30%, var(--leaf-light) 0%, rgba(216,236,122,0) 45%),
      radial-gradient(ellipse at 20% 40%, var(--leaf-deep) 0%, rgba(111,154,44,0) 55%),
      linear-gradient(180deg, var(--sky-blue) 0%, var(--leaf-deep) 40%, var(--cover-light) 100%);
  }
  .title-block {
    position: absolute;
    left: 24px;
    top: 232px;
    right: 0;
  }
  .title-main {
    font-family: 'Cinzel', serif;
    font-weight: 400;
    font-size: 46px;
    letter-spacing: 1px;
    color: var(--ink);
    line-height: 1;
  }
  .title-main .cap { font-size: 60px; }
  .title-band-row {
    display: flex;
    align-items: center;
    margin-top: 4px;
    margin-left: 150px;
  }
  .title-band {
    flex: 1;
    background: var(--band-green);
    color: var(--paper-white);
    font-family: 'Open Sans', sans-serif;
    font-size: 22px;
    line-height: 1;
    padding: 3px 10px 5px;
  }
  .synopsis {
    position: absolute;
    left: 24px;
    top: 336px;
    width: 510px;
    font-family: 'Open Sans', sans-serif;
    font-size: 17.5px;
    line-height: 1.38;
    color: var(--ink);
  }
  .synopsis p + p { margin-top: 20px; }
  .author-signature {
    position: absolute;
    left: 290px;
    top: 800px;
    width: 180px;
    height: 50px;
    background: rgba(255,255,255,0.12);
  }
  .spine {
    position: relative;
    width: 100px;
    height: 896px;
    background: linear-gradient(180deg, #3b7a30 0%, var(--spine-green) 30%, var(--spine-green) 100%);
  }
  .spine-author {
    position: absolute;
    top: 30px;
    left: 0; right: 0;
    margin: 0 auto;
    writing-mode: vertical-rl;
    font-family: 'Open Sans', sans-serif;
    font-size: 20px;
    color: var(--paper-white);
    text-align: center;
    width: 100%;
    display: flex;
    justify-content: center;
  }
  .spine-title {
    position: absolute;
    top: 360px;
    left: 0;
    width: 100%;
    writing-mode: vertical-rl;
    display: flex;
    align-items: center;
    gap: 14px;
    color: var(--paper-white);
  }
  .spine-title-main {
    font-family: 'Cinzel', serif;
    font-weight: 600;
    font-size: 44px;
    letter-spacing: 1px;
  }
  .spine-title-sub {
    font-family: 'Open Sans', sans-serif;
    font-size: 30px;
  }
</style>
</head>
<body>
  <main class="book-wrap">
    <section class="back-cover">
      <div class="leaf-photo" role="img" aria-label="Close-up photo of bright green new leaves against a soft blurred background"></div>

      <div class="title-block">
        <h1 class="title-main"><span class="cap">Q</span>UIET <span class="cap">R</span>OOMS</h1>
        <div class="title-band-row">
          <span class="title-band">Within</span>
        </div>
      </div>

      <div class="synopsis">
        <p>Quiet Rooms Within is an acutely honest and often highly entertaining memoir by Daphne Korrel about life with Asperger's Syndrome.</p>
        <p>The book follows Daphne in exploring her past and takes the reader with her on her journey to receiving and accepting her diagnosis. Instead of rehashing widely available Asperger's information, Daphne focuses on discussing the thoughts, feelings and ideas that go along with being an Aspie, giving us a rare peek into what it really feels like to be a person on the spectrum. A must read for all those who enjoy deep personal stories or have a loved one on the spectrum that they wish to understand better.</p>
      </div>

      <div class="author-signature" role="img" aria-label="Handwritten author signature"></div>
    </section>

    <aside class="spine">
      <div class="spine-author">Daphne Korrel</div>
      <div class="spine-title">
        <span class="spine-title-main">QUIET ROOMS</span>
        <span class="spine-title-sub">Within</span>
      </div>
    </aside>
  </main>
</body>
</html>
```